A New and modern Business Card for Tarwick Trade Solutions Ltd

New and modern Logo and Business Card Attached is the current logo/business card designCurrently the business is called "Tarwick & Co." or TTS Ltd for short. This is subject to change.This business specialises in Telecoms and Energy. We work with the major networks (QV, K7, etc) and also offer Energy Products saving clients money off their energy bills.These are business to business services.The current design incorporates a Pheonix, indicating rebirth, starting something new.We would like to maintain the Phoenix element but a newer modern style.We love colours in the logo 3 max.The aim of this is to be ultra slick and modern. I envisage Tarwick & Co. on one side of the card with long descriptions on the other side.Side 1:TTS Ltd/Logo?Side 2:TTS Ltd/Logo/Graphic?Tarwick & Co..Name:Address:Phone:Email:The design is mostly flexible but must incorporate a Phoenix.For example "Tarwick & Co." with a block phoenix behind the text...up to you.

Industry/Entity Type

Telecommunications

Contact Information for Business Card

Tarwick & Co.
Address:
Name:
Phone:
Email:

Logo Text

Tarwick & Co.

Colors
33a6d7
0792cd
acd037
9bcb3c
f78f20
fece3e

Requirements
Must have
• Phoenix
• 3/4 colours max
• Blue representing Technology (wireless)
• Green for Eco Energy
• Orange for Phoenix
• White business card background
Should not have
• phoenix must not all be red/ orange fire, we are a technology service company and the phoenix colours must represent this. Fire is not representative of our company.

```html
<!DOCTYPE html>
<html lang="en">
<head>
<meta charset="utf-8">
<title>Tarwick &amp; Co. Business Card</title>
<link rel="stylesheet" href="https://fonts.googleapis.com/css2?family=Cinzel:wght@400;600&family=Lato:wght@400&display=swap">
<style>
  :root {
    --backdrop: #3b322e;
    --card-white: #f6f6f4;
    --ink-dark: #3e3e40;
    --ink-body: #4a4a4c;
    --accent-green: #8cc63f;
    --accent-orange: #e8a21a;
    --gradient-top: #d49a12;
    --gradient-mid: #6cc21c;
    --gradient-bottom: #22a98a;
    --divider: #d9d9d6;
  }
  * { box-sizing: border-box; margin: 0; padding: 0; }
  html, body {
    width: 1200px; height: 844px; overflow: hidden;
    background: var(--backdrop);
  }
  .canvas {
    position: relative; width: 1200px; height: 844px;
  }
  .card {
    position: absolute; top: 279px;
    width: 500px; height: 286px;
    box-shadow: 0 6px 18px rgba(0,0,0,0.35);
  }
  /* Front side */
  .card-front {
    left: 70px;
    background: var(--card-white);
    display: flex;
  }
  .brand-panel {
    width: 235px; height: 100%;
    display: flex; flex-direction: column;
    align-items: center; justify-content: center; gap: 14px;
  }
  .brand-dot {
    width: 58px; height: 58px; border-radius: 50%;
    background: var(--accent-green);
  }
  .brand-name {
    font-family: "Cinzel", serif; font-weight: 600;
    font-size: 26px; letter-spacing: 1px; color: var(--ink-dark);
  }
  .divider {
    width: 1px; margin: 46px 0;
    background: var(--divider);
  }
  .contact-panel {
    flex: 1; padding: 70px 0 0 24px;
    font-family: "Lato", sans-serif; color: var(--ink-body);
  }
  .person-name {
    font-family: "Cinzel", serif; font-size: 16px;
    color: var(--accent-green); letter-spacing: 0.5px;
  }
  .person-role { font-size: 13px; margin-bottom: 6px; }
  .contact-line {
    display: flex; align-items: center; gap: 7px;
    font-size: 13px; line-height: 19px;
  }
  .contact-line svg { width: 11px; height: 11px; fill: var(--accent-green); }
  .address { font-size: 13px; line-height: 17px; margin-top: 8px; }
  /* Back side */
  .card-back {
    left: 630px;
    background: linear-gradient(160deg, var(--gradient-top) 0%, var(--gradient-mid) 48%, var(--gradient-bottom) 100%);
    display: flex; align-items: center; justify-content: center; gap: 14px;
  }
  .back-dot {
    width: 44px; height: 44px; border-radius: 50%;
    background: #ffffff;
  }
  .back-name {
    font-family: "Cinzel", serif; font-weight: 600;
    font-size: 30px; letter-spacing: 1px; color: #ffffff;
  }
</style>
</head>
<body>
<main class="canvas">
  <section class="card card-front">
    <div class="brand-panel">
      <div class="brand-dot"></div>
      <div class="brand-name">Tarwick &amp; Co.</div>
    </div>
    <div class="divider"></div>
    <div class="contact-panel">
      <div class="person-name">DANIEL REEVE</div>
      <div class="person-role">Managing Director</div>
      <div class="contact-line">
        <svg viewBox="0 0 24 24"><path d="M6.6 10.8a15 15 0 0 0 6.6 6.6l2.2-2.2a1 1 0 0 1 1-.25 11.4 11.4 0 0 0 3.6.57 1 1 0 0 1 1 1V20a1 1 0 0 1-1 1A17 17 0 0 1 3 4a1 1 0 0 1 1-1h3.5a1 1 0 0 1 1 1c0 1.25.2 2.45.57 3.57a1 1 0 0 1-.25 1z"/></svg>
        <span>044-321 654 987</span>
      </div>
      <div class="contact-line">
        <svg viewBox="0 0 24 24"><path d="M2 5h20v14H2z M2 5l10 8 10-8" /></svg>
        <span>hello@tarwickco.com</span>
      </div>
      <div class="address">17, Harbour Lane here,<br>30218,Country Name</div>
    </div>
  </section>
  <section class="card card-back">
    <div class="back-dot"></div>
    <div class="back-name">Tarwick &amp; Co.</div>
  </section>
</main>
</body>
</html>
```